Create Website for new company called "Verdale Lodge 37"

Verdale Lodge 37 is a new business situated in Southwestern Colorado. We are creating a business that will rent out spaces where clients can grow their own marijuana. Picture a large green house with partitioned spaces that are secured by a lock. Best way to envision this would be to think of a storage business that rents out storage rooms. The difference is that we will be having the units inside a green house ( for growing purposes) Picture a small area that is secured by locks, Picture an area that has the ability to provide state of the art security, cameras etc. We want to focus our efforts on professionals, blue collar workers and end users of marijuana. Our emphasis is in the area of assisting those whom wish to grow their own plants. We want to provide them a safe facility in which to do that. . Keep in mind that we also build custom grow rooms at clients homes and provide a grow pod (lease these) where a small grow unit will be delivered and picked up from our clients whom want to lease a unit for a short amount of time. We have a business card ( just designed) and will send that information to those whom express an interests in this project. We want to be able to sign people up for our services by entering an agreement and signing the agreement while on the internet. We want to provide our services to those whom consume recreational and medical marijuana. This site will need to gather information I.e email addresses so that we can followup with offers. This is a tremendous opportunity for the right designer. We will be creating many more websites as other states come on line and make marijuana legal to consume. Use the business card model for a point of reference of how we envision the concept. That is a business card we just recently printed. The hands and the plant is our logo so far. Open to suggestions. There will be three levels of service. Bronze, Silver, Gold or Platinum. We will also have a retail biz down the road but not at the present time.

Target Market(s)

Ages 21-60

Industry/Entity Type

Medical

Logo Text

Verdale Lodge 37.

Number of Pages Required

5+ page

Requirements
Must have
• Clean appearance not to busy , easily navigable from link to link, page to page. Must have ability down the road to enter into a contractual agreement via the website. Must use our provided logo and example of that is on our business card that will be uploaded here shortly. We would like to have the colors that are on the business card however if you have suggestions or color schemes that you want us to consider that is okay.
Nice to have
• Nice to have a animation of seed to weed and how clients can save a tremendous amount of money growing their own cannabis. Nice to have testimonial page or feedback page. Have a membership component to website,
Should not have
• No flashing lights, etc. Not to busy in terms of animations.

```html
<!DOCTYPE html>
<html lang="en">
<head>
<meta charset="utf-8">
<title>Verdale Lodge 37</title>
<link href="https://fonts.googleapis.com/css2?family=Roboto+Condensed:wght@400;700&family=Open+Sans:wght@400;600;700&family=Lato:ital,wght@0,400;0,700;1,400&display=swap" rel="stylesheet">
<style>
:root{
  --green:#0b8a41;
  --green-dark:#06692f;
  --green-light:#12a04e;
  --white:#ffffff;
  --text:#666666;
  --text-dark:#333333;
  --panel:#f7f7f7;
  --grey-box:#676767;
  --footer:#333333;
  --footer-line:#4a4a4a;
  --field:#2c2c2c;
}
*{margin:0;padding:0;box-sizing:border-box}
html,body{width:780px;height:1200px;overflow:hidden}
body{position:relative;background:var(--white);font-family:"Lato",sans-serif;color:var(--text)}
.abs{position:absolute}
.heading{font-family:"Roboto Condensed",sans-serif}

/* header */
.topbar{left:0;top:0;width:780px;height:52px;background:linear-gradient(var(--green-dark),var(--green-light))}
.phone{left:85px;top:17px;color:var(--white);font-size:16px;font-family:"Open Sans",sans-serif;display:flex;align-items:center;gap:6px;line-height:20px}
.social{display:flex;gap:6px}
.social span{width:22px;height:22px;border-radius:50%;background:var(--white);display:block}
.social-top{left:590px;top:15px}
.nav{left:0;top:52px;width:780px;height:36px;background:var(--white)}
.nav a{position:absolute;top:0;height:36px;line-height:36px;font-size:9px;font-weight:600;color:var(--text-dark);text-decoration:none;font-family:"Open Sans",sans-serif;white-space:nowrap}
.nav a.current{background:var(--green);color:var(--white);width:60px;text-align:center;height:24px;line-height:24px;top:6px}
.nav .sep{position:absolute;top:8px;width:1px;height:20px;background:#cfcfcf}
.brand{left:303px;top:6px;width:174px;height:96px;background:var(--white);border:3px solid #3aa163;display:flex;align-items:center;justify-content:center;flex-direction:column;gap:6px}
.brand .mark{width:22px;height:22px;border-radius:50%;background:var(--green)}
.brand .name{font-family:"Roboto Condensed",sans-serif;font-weight:700;font-size:19px;color:var(--text-dark);white-space:nowrap}

/* hero */
.hero{left:0;top:88px;width:780px;height:311px;background:radial-gradient(ellipse at 40% 55%,#6f9a45 0%,#3d6a2a 35%,#1f3e1a 70%,#142a12 100%)}
.arrow{width:30px;height:30px;border:2px solid #cfcfcf;border-radius:50%;top:228px;display:flex;align-items:center;justify-content:center}
.caption{left:417px;top:270px;width:278px;height:66px;background:rgba(20,30,18,.72);color:var(--white);font-family:"Roboto Condensed",sans-serif;font-size:21px;line-height:29px;text-align:right;padding:4px 18px 0 0;white-space:nowrap}

/* features */
.features-bg{left:0;top:399px;width:780px;height:208px;background:var(--panel)}
.card{top:364px;width:188px;height:213px;background:var(--white);border:1px solid #bdbdbd;border-radius:0 0 6px 6px;box-shadow:0 12px 10px -10px rgba(0,0,0,.35)}
.card h3{height:36px;background:linear-gradient(var(--green-light),var(--green-dark));color:var(--white);font-family:"Roboto Condensed",sans-serif;font-weight:400;font-size:16px;line-height:36px;padding-left:13px;border-radius:4px 4px 0 0;margin:-1px -1px 0}
.card .photo{margin:10px 0 0 10px;width:168px;height:72px;border:3px solid #666}
.card p{font-size:9px;line-height:15px;margin:8px 10px 0;height:60px;overflow:hidden;color:#777}
.more{font-size:8px;font-weight:700;color:var(--text-dark);text-decoration:underline;font-family:"Lato",sans-serif;white-space:nowrap}
.card .more{position:absolute;left:11px;top:188px}

/* welcome */
.welcome{left:0;top:607px;width:780px;height:183px;background:linear-gradient(var(--green-light),var(--green-dark))}
.video{left:85px;top:625px;width:188px;height:146px;background:linear-gradient(135deg,#6e8a3e,#3f5a27 55%,#2a3f1c)}
.video .controls{position:absolute;left:0;bottom:0;width:188px;height:21px;background:#111;display:flex;align-items:center;gap:6px;padding:0 6px;color:var(--white);font-size:7px}
.video .track{width:72px;height:4px;background:#555;border-radius:2px;position:relative}
.video .track i{position:absolute;left:0;top:0;width:56px;height:4px;background:#888;border-radius:2px}
.welcome-title{left:296px;top:623px;color:var(--white);font-size:19px;white-space:nowrap}
.welcome-rule{left:296px;top:650px}
.welcome-text{left:296px;top:662px;width:400px;color:var(--white);font-size:9.2px;line-height:15px}
.welcome-text p{max-height:45px;overflow:hidden}
.welcome-text p+p{margin-top:14px;max-height:30px}
.welcome-more{left:296px;top:755px;color:var(--white)}

/* testimonial & news */
.info{left:0;top:790px;width:780px;height:225px;background:linear-gradient(#f6f6f6,#e0e0e0)}
.sec-title{display:flex;align-items:center;gap:8px;font-family:"Roboto Condensed",sans-serif;font-size:16px;color:var(--text-dark);white-space:nowrap}
.quote{left:85px;top:854px;width:281px;height:107px;background:var(--grey-box);border-radius:3px;color:var(--white);font-size:8.6px;line-height:15px;font-style:italic;padding:14px 16px 0 18px;text-indent:16px;overflow:hidden}
.quote-name{left:142px;top:967px;font-weight:700;font-size:10px;color:var(--text-dark)}
.divider{left:389px;top:848px;width:2px;height:130px;background:linear-gradient(transparent,#c5c5c5,transparent)}
.news-item{left:415px;width:280px}
.news-date{font-weight:700;font-size:9px;color:var(--text-dark);display:flex;gap:5px;align-items:center}
.news-date i{width:7px;height:7px;background:#bbb;display:block}
.news-head{font-weight:700;font-size:9.8px;color:#555;margin:3px 0 0 12px;white-space:nowrap}
.news-body{font-size:8.3px;line-height:14px;margin-left:12px;color:#888;max-height:28px;overflow:hidden}

/* footer */
.footer{left:0;top:1015px;width:780px;height:185px;background:var(--footer)}
.quote-panel{left:85px;top:1015px;width:190px;height:185px;background:#2e2e2e;box-shadow:4px 0 8px rgba(0,0,0,.35)}
.foot-title{color:var(--white);font-family:"Roboto Condensed",sans-serif;font-size:14px;white-space:nowrap}
.field{left:97px;width:164px;background:var(--field);border:1px solid #555;color:#9a9a9a;font-size:7px;padding:5px 7px}
.btn{background:var(--green);color:var(--white);font-size:10px;font-family:"Open Sans",sans-serif;display:flex;align-items:center;justify-content:center}
.footer-rule{height:1px;background:var(--footer-line)}
.foot-text{color:#dcdcdc;font-size:8.6px;line-height:14px}
</style>
</head>
<body>

<header>
  <div class="abs topbar"></div>
  <div class="abs phone">
    <svg width="18" height="18" viewBox="0 0 18 18"><circle cx="9" cy="9" r="8" fill="none" stroke="#fff" stroke-width="1.5"/><path d="M6 5.2c.5-.4 1-.3 1.3.2l.7 1.2c.2.4.1.8-.2 1l-.5.4c.4 1 1.2 1.8 2.2 2.2l.4-.5c.3-.3.7-.4 1-.2l1.2.7c.5.3.6.8.2 1.3l-.5.6c-.6.6-2 .5-3.8-1.1C6.2 9.3 5.4 7.8 5.6 6.1z" fill="#fff"/></svg>
    +123-456-7890
  </div>
  <div class="abs social social-top" aria-label="Social links"><span></span><span></span><span></span><span></span></div>

  <nav class="abs nav">
    <a class="current" style="left:85px">HOME</a>
    <a style="left:165px">ABOUT US</a>
    <span class="sep" style="left:224px"></span>
    <a style="left:245px">SERVICES</a>
    <a style="left:499px">FACILITIES</a>
    <span class="sep" style="left:548px"></span>
    <a style="left:559px">TESTIMONIAL</a>
    <span class="sep" style="left:621px"></span>
    <a style="left:634px">CONTACT US</a>
    <span class="sep" style="left:694px"></span>
  </nav>

  <div class="abs brand"><span class="mark"></span><span class="name">VERDALE LODGE 37</span></div>
</header>

<section>
  <div class="abs hero" role="img" aria-label="Close-up photo of green leafy plants in a grow room"></div>
  <div class="abs arrow" style="left:55px"><svg width="10" height="12" viewBox="0 0 10 12"><path d="M7 1 2 6l5 5" fill="none" stroke="#fff" stroke-width="1.6"/></svg></div>
  <div class="abs arrow" style="left:694px"><svg width="10" height="12" viewBox="0 0 10 12"><path d="M3 1l5 5-5 5" fill="none" stroke="#fff" stroke-width="1.6"/></svg></div>
  <div class="abs caption">Lorem ipsum dolor sit amet,<br>consectetuer adipiscing elit, sed</div>
</section>

<section>
  <div class="abs features-bg"></div>
  <article class="abs card" style="left:85px">
    <h3>HELP U GROW</h3>
    <div class="photo" role="img" aria-label="Photo of hands holding soil with a seedling" style="background:linear-gradient(135deg,#6b5a48,#3a2c20)"></div>
    <p>Lorem ipsum dolor sit ametuer adipiscingi elit, sed diam nmy nibh euismod tincidunt ut laoreet dolore magna am erat visi enim ad minim veniam, quis nostrud exerci</p>
    <span class="more">READ MORE »</span>
  </article>
  <article class="abs card" style="left:296px">
    <h3>SECURITY</h3>
    <div class="photo" role="img" aria-label="Photo of a security camera on a brick wall" style="background:linear-gradient(90deg,#5d8fd6,#7aa8e4 60%,#9a5a44)"></div>
    <p>Lorem ipsum dolor sit ametuer adipiscingi elit, sed diam nmy nibh euismod tincidunt ut laoreet dolore magna am erat visi enim ad minim veniam, quis nostrud exerci</p>
    <span class="more">READ MORE »</span>
  </article>
  <article class="abs card" style="left:507px">
    <h3>ONLINE ACCESS</h3>
    <div class="photo" role="img" aria-label="Photo of a screen showing the website" style="background:linear-gradient(90deg,#2a2a2a 0%,#f2f2f2 10%,#f2f2f2 100%)"></div>
    <p>Lorem ipsum dolor sit ametuer adipiscingi elit, sed diam nmy nibh euismod tincidunt ut laoreet dolore magna am erat visi enim ad minim veniam, quis nostrud exerci</p>
    <span class="more">READ MORE »</span>
  </article>
</section>

<section>
  <div class="abs welcome"></div>
  <div class="abs video" role="img" aria-label="Video of a grow room full of plants">
    <svg style="position:absolute;left:83px;top:55px" width="24" height="24" viewBox="0 0 24 24"><circle cx="12" cy="12" r="11" fill="#fff"/><path d="M9.5 7v10l8-5z" fill="#333"/></svg>
    <div class="controls">
      <svg width="8" height="9" viewBox="0 0 8 9"><path d="M0 0v9l8-4.5z" fill="#fff"/></svg>
      <span>04:59</span>
      <span class="track"><i></i></span>
      <span>10:35</span>
      <svg width="10" height="9" viewBox="0 0 10 9"><path d="M0 3h2l3-3v9L2 6H0z" fill="#fff"/><path d="M7 2c1 1.3 1 3.7 0 5" stroke="#fff" fill="none"/></svg>
      <svg width="9" height="9" viewBox="0 0 9 9"><path d="M1 1l7 7M1 1h3M1 1v3M8 8H5M8 8V5" stroke="#fff" fill="none"/></svg>
    </div>
  </div>
  <h2 class="abs heading welcome-title" style="font-weight:400">Welcome To Verdale Lodge 37</h2>
  <svg class="abs welcome-rule" width="400" height="8" viewBox="0 0 400 8"><path d="M0 1h14l5 5 5-5h376" fill="none" stroke="rgba(255,255,255,.55)"/></svg>
  <div class="abs welcome-text">
    <p>Lorem ipsum dolor sit amet, consectetuer adipiscing elit, sed diam nonummy nibh euismod ut laoreet dolore magna aliquam erat volutpat. Ut wisi enim ad minim veniam, quis nostrud etation ullamcorper suscipit lobortis nisl ut aliquip ex ea commodo consequat.</p>
    <p>Duis autem vel eum iriure dor in hendrerit in vulputate velit esse molestie &nbsp;vel illum dolore eu feugiat nulla facilisro eros et accumsan et iusto odio dignissim qui blandit praesent luptatum zzril.</p>
  </div>
  <span class="abs more welcome-more">READ MORE »</span>
</section>

<section>
  <div class="abs info"></div>
  <div class="abs sec-title" style="left:87px;top:811px">
    <svg width="19" height="17" viewBox="0 0 19 17"><path d="M1 1h11v7H6l-3 3V8H1z" fill="var(--green)"/><path d="M14 5h4v7h-2v3l-3-3H7V10h6z" fill="var(--green)"/></svg>
    Client Testimonial
  </div>
  <svg class="abs" style="left:85px;top:832px" width="282" height="8" viewBox="0 0 282 8"><path d="M0 5h8l4-4 4 4h266" fill="none" stroke="#777"/></svg>
  <blockquote class="abs quote">Lorem ipsum dolor sit amet, consectetuer adipi sed diam nony nibh euismod ut laoreet dolore magna aliquam erat volut wisi enim ad minim veniam, quis nostrud etation ullamcorpecipit lobortis nisl ut aliquip ex ea commodo consequatuis autem vel eum iriure dor in hendrerit in vulputate velit esse molestie &nbsp;vel illum dolore</blockquote>
  <svg class="abs" style="left:102px;top:868px" width="15" height="12" viewBox="0 0 15 12"><path d="M1 12V6c0-3 2-5 5-6v2C4 3 4 4 4 6h2v6zM9 12V6c0-3 2-5 5-6v2c-2 1-2 2-2 4h2v6z" fill="#bbb"/></svg>
  <svg class="abs" style="left:317px;top:930px" width="15" height="12" viewBox="0 0 15 12"><path d="M14 0v6c0 3-2 5-5 6v-2c2-1 2-2 2-4H9V0zM6 0v6c0 3-2 5-5 6v-2C3 9 3 8 3 6H1V0z" fill="#bbb"/></svg>
  <svg class="abs" style="left:108px;top:960px" width="26" height="14" viewBox="0 0 26 14"><path d="M0 0h26L24 13z" fill="var(--grey-box)"/></svg>
  <div class="abs quote-name">Mr. Nisl Ut Aliquip</div>

  <div class="abs divider"></div>

  <div class="abs sec-title" style="left:415px;top:811px">
    <svg width="20" height="16" viewBox="0 0 20 16"><path d="M1 5h4l9-4v14l-9-4H1z" fill="var(--green)"/><path d="M4 11l2 5h2l-1-5z" fill="var(--green)"/><path d="M16 5l3-2M16 8h3M16 11l3 2" stroke="var(--green)" stroke-width="1.4"/></svg>
    Latest News
  </div>
  <svg class="abs" style="left:415px;top:832px" width="280" height="8" viewBox="0 0 280 8"><path d="M0 5h8l4-4 4 4h264" fill="none" stroke="#777"/></svg>
  <div class="abs news-item" style="top:854px">
    <div class="news-date"><i></i>14-March-2014</div>
    <div class="news-head">Exerci tation ullamcorper suscipit lobortis nisl ut aliquip.</div>
    <div class="news-body">Lorem ipsum dolor sit amet, consectetuer adipiscing eli sed di nonmmy nibh euismod tincidunt ut laoreet dolore ma aliquam erat volutpat.</div>
  </div>
  <div class="abs" style="left:415px;top:916px;width:280px;border-top:1px dotted #888"></div>
  <div class="abs news-item" style="top:930px">
    <div class="news-date"><i></i>14-March-2014</div>
    <div class="news-head">Mullamcorper suscipit lobortis nisl ut aliquip.</div>
    <div class="news-body">nibh euismod tincidunt ut laoreet dolore ma aliquam erat volutpat.</div>
  </div>
</section>

<footer>
  <div class="abs footer"></div>
  <div class="abs quote-panel"></div>
  <div class="abs foot-title" style="left:98px;top:1027px;display:flex;gap:8px;align-items:center;font-size:15px">
    <svg width="20" height="16" viewBox="0 0 20 16"><path d="M1 6 10 1l9 5v9H1z" fill="none" stroke="#fff" stroke-width="1.5"/><path d="M1 6l9 6 9-6" fill="none" stroke="#fff" stroke-width="1.5"/></svg>
    Request a Quote
  </div>
  <div class="abs field" style="top:1056px;height:21px">Name</div>
  <div class="abs field" style="top:1082px;height:23px">Email</div>
  <div class="abs field" style="top:1111px;height:42px">Message</div>
  <div class="abs btn" style="left:97px;top:1163px;width:49px;height:23px">SEND</div>

  <div class="abs foot-title" style="left:296px;top:1027px">News Latter Signup</div>
  <div class="abs" style="left:296px;top:1052px;width:185px;height:24px;background:#6a6a6a;color:#eee;font-size:7.5px;line-height:24px;padding-left:9px">Enter Your Email</div>
  <div class="abs btn" style="left:486px;top:1052px;width:55px;height:24px">SUBMIT</div>
  <div class="abs" style="left:563px;top:1038px;width:1px;height:44px;background:var(--footer-line)"></div>

  <div class="abs foot-title" style="left:590px;top:1027px">Socail Connect</div>
  <div class="abs social" style="left:590px;top:1053px" aria-label="Social links"><span></span><span></span><span></span><span></span></div>

  <div class="abs footer-rule" style="left:296px;top:1093px;width:399px"></div>
  <svg class="abs" style="left:296px;top:1108px" width="9" height="13" viewBox="0 0 9 13"><path d="M4.5 0C2 0 0 2 0 4.5 0 8 4.5 13 4.5 13S9 8 9 4.5C9 2 7 0 4.5 0zm0 6.3a1.8 1.8 0 1 1 0-3.6 1.8 1.8 0 0 1 0 3.6z" fill="#fff"/></svg>
  <div class="abs foot-text" style="left:314px;top:1106px;width:95px">Lorem ipsum dolor sit amet, consectetuer adipiscing eli sed di nonmmy</div>
  <svg class="abs" style="left:428px;top:1108px" width="8" height="12" viewBox="0 0 8 12"><rect x=".5" y=".5" width="7" height="11" rx="1.5" fill="none" stroke="#fff"/><rect x="2" y="2" width="4" height="6" fill="#fff"/></svg>
  <div class="abs foot-text" style="left:445px;top:1106px;font-size:10px">123-456-7890</div>
  <svg class="abs" style="left:427px;top:1132px" width="11" height="9" viewBox="0 0 11 9"><path d="M0 3 5.5 0 11 3v6H0z" fill="#fff"/><path d="M0 3l5.5 3.5L11 3" fill="none" stroke="#333"/></svg>
  <div class="abs foot-text" style="left:445px;top:1130px">info@verdalelodge37.com</div>
  <div class="abs" style="left:563px;top:1102px;width:1px;height:48px;background:var(--footer-line)"></div>
  <div class="abs" style="left:582px;top:1114px;display:flex;align-items:center;gap:6px">
    <span style="width:14px;height:14px;border-radius:50%;background:var(--green);display:block"></span>
    <span class="heading" style="color:#dcdcdc;font-weight:700;font-size:14px;white-space:nowrap">VERDALE LODGE 37</span>
  </div>
  <div class="abs footer-rule" style="left:296px;top:1163px;width:399px"></div>
  <div class="abs foot-text" style="left:305px;top:1175px">© 2014 Verdale Lodge &nbsp;| &nbsp;All Rights Reserved</div>
</footer>

</body>
</html>
```